business card - for laser marking

I need design (curve) for my business card (make with laser) size 85mm x 55mm. How it look business card with laser marking see attached picture.

color:
Background: white
text and icons black

Please include: one side
1. dominik vrabec - direktor
2. phone: +386(0)41 726 190
+386(0)580 237 61
3. info@zarezko.example
4. faecebook.com/Zarezko.Ex
5. KM-ATELJE, Dominik Vrabec s.p.
Lipova ulica 19, 1000 Ljubljana, SI
6. logo

Please include: second side
1. logo
2. www.zarezko.example
3. Lasersko graviranje
ovitki telefonov, ohišja telefonov / tablic, nakit, ure, alu vizitke, dog-tagi, kemični svinčniki, orodja, noži, vžigalniki

Industry/Entity Type

Business

Contact Information for Business Card

Please include: one side
+386(0)580 237 61
3. info@zarezko.example
6. logo

1. logo
2. www.zarezko.example
3. Lasersko graviranje

Colors
000000
ffffff

Requirements
Must have
• I need design (curve) for my business card (make with laser) size 85mm x 55mm. How it look business card with laser marking see attached picture.
• color:
• Background: white
• text and icons black
• Please include: one side
• 1. dominik vrabec - direktor
• 2. phone: +386(0)41 726 190
• +386(0)580 237 61
• 3. info@zarezko.example
• 4. faecebook.com/Zarezko.Ex
• 5. KM-ATELJE, Dominik Vrabec s.p.
• Lipova ulica 19, 1000 Ljubljana, SI
• 6. logo
• Please include: second side
• 1. logo
• 2. www.zarezko.example
• 3. Lasersko graviranje
• ovitki telefonov, ohišja telefonov / tablic, nakit, ure, alu vizitke, dog-tagi, kemični svinčniki, orodja, noži, vžigalniki

```html
<!DOCTYPE html>
<html lang="sl">
<head>
<meta charset="utf-8">
<title>Zarezko – vizitka</title>
<link rel="stylesheet" href="https://fonts.googleapis.com/css2?family=Open+Sans:wght@400;600;700&display=swap">
<style>
  :root {
    --bg: #e6e1da;
    --card-dark: #1f2021;
    --card-light: #ffffff;
    --accent-pink: #d6155a;
    --accent-green: #5da12f;
    --text-light: #f2f2f2;
    --text-grey: #555555;
  }
  * { box-sizing: border-box; margin: 0; padding: 0; }
  html, body { width: 1200px; height: 911px; overflow: hidden; }
  body {
    background: var(--bg);
    font-family: "Open Sans", Arial, sans-serif;
    position: relative;
  }
  .card {
    position: absolute;
    border-radius: 22px;
    box-shadow: 0 10px 28px rgba(0,0,0,.25);
    overflow: hidden;
  }
  /* front side */
  .card-front {
    left: 100px; top: 162px;
    width: 380px; height: 587px;
    background: var(--card-dark);
    color: var(--text-light);
    text-align: center;
    padding-top: 78px;
  }
  .brand {
    display: inline-flex; align-items: center; gap: 12px;
    font-weight: 700; color: var(--accent-pink);
    letter-spacing: 2px;
  }
  .brand-dot {
    width: 22px; height: 22px; border-radius: 50%;
    background: var(--accent-pink);
  }
  .card-front .brand { font-size: 40px; }
  .holder-name {
    margin-top: 62px;
    font-size: 21px; font-weight: 700; letter-spacing: 1px;
    color: var(--accent-pink);
    text-transform: uppercase;
  }
  .holder-role {
    font-size: 15px; font-weight: 700; letter-spacing: 1px;
    color: var(--accent-green);
  }
  .contact-list { list-style: none; margin-top: 12px; }
  .contact-item {
    display: flex; flex-direction: column; align-items: center;
    font-size: 15px; line-height: 20px;
    margin-bottom: 6px;
  }
  .contact-icon { width: 14px; height: 14px; margin-bottom: 3px; fill: var(--accent-pink); }
  /* back side */
  .card-back {
    left: 520px; top: 265px;
    width: 587px; height: 380px;
    background: var(--card-light);
    padding: 72px 60px 0 70px;
  }
  .card-back .brand { font-size: 58px; letter-spacing: 4px; }
  .card-back .brand-dot { width: 30px; height: 30px; }
  .service-title {
    margin-top: 16px;
    font-size: 16px; color: var(--text-grey);
  }
  .service-list {
    margin-top: 6px;
    font-size: 14px; line-height: 22px; color: var(--text-grey);
    max-width: 460px;
  }
  .website {
    margin-top: 34px;
    font-size: 17px; font-weight: 700; color: var(--accent-pink);
  }
</style>
</head>
<body>
  <section class="card card-front" aria-label="Sprednja stran vizitke">
    <div class="brand"><span class="brand-dot"></span>ZAREZKO</div>
    <p class="holder-name">Dominik Vrabec</p>
    <p class="holder-role">DIREKTOR</p>
    <ul class="contact-list">
      <li class="contact-item">
        <svg class="contact-icon" viewBox="0 0 14 14"><path d="M7 0a5 5 0 0 0-5 5c0 3.6 5 9 5 9s5-5.4 5-9a5 5 0 0 0-5-5zm0 7a2 2 0 1 1 0-4 2 2 0 0 1 0 4z"/></svg>
        <span>KM-ATELJE</span>
        <span>Dominik Vrabec s.p.</span>
        <span>Lipova ulica 19</span>
        <span>1000 Ljubljana, SI</span>
      </li>
      <li class="contact-item">
        <svg class="contact-icon" viewBox="0 0 14 14"><path d="M3 0l2.5 3.5-1.5 1.5c.8 2 2.5 3.7 4.5 4.5l1.5-1.5L14 10.5 12 13C5.5 13 1 8.5 1 2z"/></svg>
        <span>+386(0)580 237 61</span>
      </li>
      <li class="contact-item">
        <svg class="contact-icon" viewBox="0 0 14 14"><path d="M3 0h8v14H3zm1.5 1.5v9h5v-9z"/></svg>
        <span>+386(0)41 726 190</span>
      </li>
      <li class="contact-item">
        <svg class="contact-icon" viewBox="0 0 14 14"><path d="M0 2h14v10H0zm1.5 1.2v.6L7 7.6l5.5-3.8v-.6z"/></svg>
        <span>info@zarezko.example</span>
      </li>
      <li class="contact-item">
        <svg class="contact-icon" viewBox="0 0 14 14"><rect x="1" y="1" width="12" height="12" rx="2"/></svg>
        <span>Zarezko.Ex</span>
      </li>
    </ul>
  </section>

  <section class="card card-back" aria-label="Zadnja stran vizitke">
    <div class="brand"><span class="brand-dot"></span>ZAREZKO</div>
    <p class="service-title">Lasersko graviranje</p>
    <p class="service-list">ovitki telefonov, ohišja telefonov / tablic, nakit, ure, alu vizitke, dog-tagi, kemični svinčniki, orodja, noži, vžigalniki</p>
    <p class="website">www.zarezko.example</p>
  </section>
</body>
</html>
```